Modern looking signage for dental office.

Exterior signage for passing cars
Updates
Need extra days to review
Target Market(s)
Cars passing by
Font styles to use
Sans Serif
Colors
3276b5
Requirements
Must have
- Logo
- OPEN ON SUTURDAY AND SUNDAY
- NIGHT CLINIC AVAILABLE
- PLEASE USE THE FONT TYPE IN FILE 4 UPLOADED BELOW.
- (847) 302-7469
- Modern looking

```html
<!DOCTYPE html>
<html lang="en">
<head>
<meta charset="utf-8">
<title>Arc Dental – Exterior Sign</title>
<link rel="stylesheet" href="https://fonts.googleapis.com/css2?family=Josefin+Sans:wght@400&family=Francois+One&family=Open+Sans:wght@700&display=swap">
<style>
  :root {
    --page: #ffffff;
    --paper: #f2f2f2;
    --ink: #555353;
    --teal: #17808f;
    --teal-dark: #147a87;
    --blue-light: #1a9699;
    --blue-edge: #10759a;
    --white: #ffffff;
  }
  * { margin: 0; padding: 0; box-sizing: border-box; }
  html, body {
    width: 1200px; height: 1000px; overflow: hidden;
    background: var(--page);
  }
  .sign {
    position: absolute; left: 62px; top: 170px;
    width: 1076px; height: 662px;
    overflow: hidden;
    background: radial-gradient(ellipse 60% 70% at 50% 62%, var(--blue-light), var(--blue-edge));
    border: 1px solid #5a5a5a;
  }
  .sign-shapes { position: absolute; inset: 0; }
  .brand-mark {
    position: absolute; left: 135px; top: 17px;
    width: 172px; height: 176px;
    border: 3px solid var(--ink); border-radius: 50%;
  }
  .brand-name {
    position: absolute; left: 322px; top: 52px;
    font-family: "Josefin Sans", sans-serif; font-weight: 400;
    font-size: 100px; line-height: 1; letter-spacing: 4px;
    color: var(--ink); white-space: nowrap;
  }
  .tagline {
    position: absolute; left: 386px; top: 166px;
    font-family: "Josefin Sans", sans-serif; font-weight: 400;
    font-size: 31px; letter-spacing: 2.5px; color: var(--ink);
    white-space: nowrap;
  }
  .night-clinic {
    position: absolute; left: 284px; top: 256px; width: 508px;
    border-top: 2px solid var(--teal); border-bottom: 2px solid var(--teal);
    height: 71px;
    display: flex; align-items: center; justify-content: center;
    font-family: "Francois One", sans-serif; font-size: 40px;
    letter-spacing: 3px; color: var(--teal);
  }
  .phone {
    position: absolute; left: 0; right: 0; top: 445px;
    display: flex; align-items: center; justify-content: center; gap: 30px;
    font-family: "Open Sans", sans-serif; font-weight: 700;
    font-size: 84px; line-height: 1; color: var(--white);
  }
  .phone-icon { width: 80px; height: 80px; }
  .divider {
    position: absolute; left: 38px; right: 38px; top: 595px; height: 2px;
    background: linear-gradient(90deg, transparent, var(--white) 20%, var(--white) 80%, transparent);
  }
  .weekend {
    position: absolute; left: 0; right: 0; top: 604px;
    text-align: center;
    font-family: "Open Sans", sans-serif; font-weight: 700;
    font-size: 38px; letter-spacing: 3px; color: var(--white);
  }
</style>
</head>
<body>
  <div class="sign">
    <svg class="sign-shapes" viewBox="0 0 1076 662" width="1076" height="662" aria-hidden="true">
      <path d="M0 0 H1076 V278 Q538 560 0 278 Z" fill="var(--white)"/>
      <path d="M0 0 H1076 V258 Q538 540 0 258 Z" fill="var(--teal-dark)"/>
      <path d="M0 0 H1076 V243 Q538 517 0 243 Z" fill="var(--paper)"/>
    </svg>

    <div class="brand-mark"></div>
    <div class="brand-name">ARC DENTAL</div>
    <div class="tagline">MODERN GENERAL DENTISTRY</div>

    <div class="night-clinic">NIGHT CLINIC AVAILABLE</div>

    <div class="phone">
      <svg class="phone-icon" viewBox="0 0 80 80" aria-hidden="true">
        <circle cx="40" cy="40" r="36" fill="none" stroke="var(--white)" stroke-width="4"/>
        <circle cx="40" cy="40" r="29" fill="none" stroke="var(--white)" stroke-width="3"/>
        <path d="M36 22 h6 v12 h-4 q-3 6 0 12 h4 v12 h-6 q-10 -18 0 -36 Z" fill="var(--white)"/>
      </svg>
      <span class="phone-number">(847) 302-7469</span>
    </div>

    <div class="divider"></div>
    <div class="weekend">OPEN ON SATURDAY AND SUNDAY</div>
  </div>
</body>
</html>
```